co working space / serviced office/ business centre

Brevlo - brevlo.in, is a very young brand bieng run by 3 young entrepreneurs. We want to be become out of the league company delivering fabulous and beautiful serviced offices in India and abroad. We hire designers who have made spaces across the world. We want to get visiting card design which gives complete fresh look to the people who carries that card, has to be very impactful and should symbolise happy young and energetic brand. should be completely out of the box thinking of international level, should portray global brand image.

Target Market(s)

Startups, (Small, medium and large corporates)

Industry/Entity Type

Business

Contact Information for Business Card

Name, Email, Address, Mobile number, Landline number, website

Colors

Designer to choose colors to be used in the design.

Requirements
Must have
• Nice new shape
Nice to have
• We want creative cuts, different size and impactful brand clarity
Should not have
• Boring and regular design and shape

```html
<!DOCTYPE html>
<html lang="en">
<head>
<meta charset="utf-8">
<title>Brevlo – Business Card</title>
<link rel="stylesheet" href="https://fonts.googleapis.com/css2?family=Play:wght@700&family=Mulish:wght@400;500&display=swap">
<style>
  :root {
    --page-bg: #d8d2c9;
    --card-bg: #eeece8;
    --brand-red: #d11f2a;
    --ink: #3b3b3b;
    --band-dark: #2a2a2a;
    --band-text: #cfcfcf;
  }
  * { margin: 0; padding: 0; box-sizing: border-box; }
  html, body {
    width: 1200px; height: 1047px; overflow: hidden;
    background: var(--page-bg);
  }
  .card-shadow {
    position: absolute; left: 80px; top: 240px;
    width: 1040px; height: 566px;
    filter: drop-shadow(0 10px 18px rgba(0,0,0,0.14));
  }
  .card {
    position: relative; width: 100%; height: 100%;
    background: var(--card-bg);
    clip-path: polygon(0 0, 930px 0, 100% 110px, 100% 100%, 70px 100%, 0 496px);
    font-family: "Mulish", sans-serif;
    color: var(--ink);
  }
  .corner-accent {
    position: absolute; right: 0; top: 0;
    width: 110px; height: 110px;
    background: var(--brand-red);
    clip-path: polygon(0 0, 24px 0, 100% 86px, 100% 100%);
  }
  .brand-dot {
    position: absolute; left: 206px; top: 52px;
    width: 84px; height: 84px; border-radius: 50%;
    background: var(--brand-red);
  }
  .brand-name {
    position: absolute; left: 54px; top: 160px; width: 388px;
    text-align: center;
    font-family: "Play", sans-serif; font-weight: 700;
    font-size: 74px; line-height: 1; letter-spacing: 2px;
    color: var(--brand-red);
  }
  .brand-rule {
    position: absolute; left: 54px; top: 247px;
    width: 388px; height: 2px; background: var(--brand-red);
  }
  .tagline {
    position: absolute; left: 54px; top: 266px; width: 388px;
    text-align: center;
    font-family: "Play", sans-serif; font-weight: 700;
    font-size: 18px; letter-spacing: 3px;
    color: var(--brand-red);
  }
  .person-name {
    position: absolute; right: 55px; top: 302px;
    font-family: "Play", sans-serif; font-weight: 700;
    font-size: 42px; letter-spacing: 1px; line-height: 1;
    color: var(--brand-red);
  }
  .name-rule {
    position: absolute; left: 54px; top: 364px;
    width: 822px; height: 2px; background: var(--brand-red);
  }
  .person-title {
    position: absolute; right: 55px; top: 353px;
    font-size: 22px; color: var(--ink);
  }
  .contact-list {
    position: absolute; list-style: none;
    font-size: 22px; line-height: 32px;
  }
  .contact-list li { display: flex; align-items: center; gap: 14px; }
  .contact-list svg { width: 16px; height: 16px; fill: none; stroke: var(--brand-red); stroke-width: 2; }
  .contact-list .solid { fill: var(--brand-red); stroke: none; }
  .phones { left: 54px; top: 404px; }
  .online { right: 44px; top: 404px; }
  .online li { justify-content: flex-end; }
  .address-band {
    position: absolute; left: 0; bottom: 15px;
    width: 100%; height: 43px;
    background: linear-gradient(90deg, var(--band-dark), #3a3a3a 50%, var(--band-dark));
    color: var(--band-text);
    font-size: 22px; line-height: 43px; text-align: center;
  }
  .red-strip {
    position: absolute; left: 0; bottom: 0;
    width: 100%; height: 15px; background: var(--brand-red);
  }
</style>
</head>
<body>
  <div class="card-shadow">
    <div class="card">
      <div class="corner-accent"></div>
      <div class="brand-dot"></div>
      <div class="brand-name">BREVLO</div>
      <div class="brand-rule"></div>
      <div class="tagline">MEET. DESK. GROW</div>

      <div class="person-name">MAREN HOLT</div>
      <div class="name-rule"></div>
      <div class="person-title">Director</div>

      <ul class="contact-list phones">
        <li>
          <svg viewBox="0 0 16 16"><path class="solid" d="M3 1l3 1 1 3-2 1.5c.8 2 2.5 3.7 4.5 4.5L11 9l3 1 1 3-2 2C7 15 1 9 1 3z"/></svg>
          <span>512 555 0148</span>
        </li>
        <li>
          <svg viewBox="0 0 16 16"><rect x="4" y="1" width="8" height="14" rx="1.5"/><line x1="7" y1="12.5" x2="9" y2="12.5"/></svg>
          <span>818 555 0192</span>
        </li>
      </ul>

      <ul class="contact-list online">
        <li>
          <span>info@Brevlo.com</span>
          <svg viewBox="0 0 16 16"><rect x="1.5" y="3.5" width="13" height="9" rx="1"/><polyline points="1.5,4 8,9 14.5,4"/></svg>
        </li>
        <li>
          <span>www.Brevlo.com</span>
          <svg viewBox="0 0 16 16"><circle cx="8" cy="8" r="6.5"/><ellipse cx="8" cy="8" rx="3" ry="6.5"/><line x1="1.5" y1="8" x2="14.5" y2="8"/></svg>
        </li>
      </ul>

      <div class="address-band">1400 North Alder Road Austin, TX 78751</div>
      <div class="red-strip"></div>
    </div>
  </div>
</body>
</html>
```